Business Cards for Internet Security Company

Awesome designers! This is the opportunity to help design cards for a forward thinking network security company. They use threat information gathered from peer groups to make intelligent decisions on what threats are relevant and which arent. ( not that you need this to do designs, but just so you know where they are coming from. ) :-)

We'd like to see a two side design and the deliverables will be in illustrator 4. The logo is attached and the logo colors are attached in the JPG and I've attached a an eps of the logo and icon

Security

```html
<!DOCTYPE html>
<html lang="en">
<head>
<meta charset="utf-8">
<title>Kestrelnet Business Cards</title>
<link href="https://fonts.googleapis.com/css2?family=Exo+2:wght@400;600&display=swap" rel="stylesheet">
<style>
  :root {
    --brand-blue: #14588f;
    --band-light: #4aa8e6;
    --band-mid: #1f7cc6;
    --paper: #ffffff;
    --paper-shade: #eef0f2;
    --ink-on-blue: #ffffff;
    --stage: #e9e6e1;
    --watermark: rgba(255,255,255,0.22);
  }
  * { margin: 0; padding: 0; box-sizing: border-box; }
  html, body { width: 1200px; height: 433px; overflow: hidden; }
  body {
    background: var(--stage);
    font-family: "Exo 2", sans-serif;
    position: relative;
  }
  .card {
    position: absolute;
    top: 62px;
    width: 540px;
    height: 309px;
    background: var(--brand-blue);
    overflow: hidden;
    box-shadow: 0 4px 14px rgba(0,0,0,0.18);
  }
  .card--front { left: 40px; }
  .card--back { left: 620px; }

  .front-panel { position: absolute; inset: 0; }

  .front-brand {
    position: absolute;
    left: 22px;
    top: 190px;
    display: flex;
    align-items: center;
    gap: 8px;
    color: var(--brand-blue);
    font-size: 30px;
    font-weight: 600;
  }
  .brand-dot {
    width: 22px; height: 22px;
    border-radius: 50%;
    background: var(--brand-blue);
  }

  .contact {
    position: absolute;
    right: 30px;
    top: 30px;
    text-align: right;
    color: var(--ink-on-blue);
  }
  .contact__name {
    font-size: 22px;
    font-weight: 600;
    letter-spacing: 1px;
    text-transform: uppercase;
  }
  .contact__role {
    font-size: 14px;
    line-height: 1.3;
    margin-bottom: 22px;
  }
  .contact__address {
    font-size: 14px;
    line-height: 1.35;
    margin-bottom: 22px;
  }
  .contact__list { list-style: none; font-size: 13px; line-height: 1.85; }
  .contact__list li { display: flex; justify-content: flex-end; align-items: center; gap: 8px; }
  .contact__list svg { width: 13px; height: 13px; fill: var(--ink-on-blue); }

  .back-ring {
    position: absolute;
    left: 60px;
    top: 130px;
    width: 150px;
    height: 150px;
    border-radius: 50%;
    border: 18px solid var(--watermark);
  }
  .back-brand {
    position: absolute;
    right: 34px;
    top: 58px;
    color: var(--ink-on-blue);
    font-size: 34px;
    font-weight: 600;
    letter-spacing: 1px;
  }
</style>
</head>
<body>

<section class="card card--front" aria-label="Business card front">
  <svg class="front-panel" viewBox="0 0 540 309" preserveAspectRatio="none" aria-hidden="true">
    <defs>
      <linearGradient id="paperFade" x1="0" y1="0" x2="1" y2="0">
        <stop offset="0" stop-color="var(--paper-shade)"/>
        <stop offset="1" stop-color="var(--paper)"/>
      </linearGradient>
    </defs>
    <path d="M0 0 H190 Q265 150 238 309 H0 Z" fill="var(--band-light)"/>
    <path d="M0 0 H178 Q252 150 226 309 H0 Z" fill="var(--band-mid)"/>
    <path d="M0 0 H166 Q240 150 214 309 H0 Z" fill="url(#paperFade)"/>
  </svg>

  <div class="front-brand">
    <span class="brand-dot"></span>
    <span class="brand-name">Kestrelnet</span>
  </div>

  <div class="contact">
    <p class="contact__name">Dana Whitcombe</p>
    <p class="contact__role">Chief Executive Officer<br>&amp; Co-Founder</p>
    <p class="contact__address">27, 9th Floor Plaza<br>Meridian Road KLT</p>
    <ul class="contact__list">
      <li>014 782 3310
        <svg viewBox="0 0 16 16"><path d="M3.5 1h3l1.2 3.5-1.8 1.3a9 9 0 0 0 4.3 4.3l1.3-1.8L15 9.5v3A1.5 1.5 0 0 1 13.5 14 12.5 12.5 0 0 1 2 2.5 1.5 1.5 0 0 1 3.5 1z"/></svg>
      </li>
      <li>014 782 3311
        <svg viewBox="0 0 16 16"><path d="M4 0h8a1 1 0 0 1 1 1v14a1 1 0 0 1-1 1H4a1 1 0 0 1-1-1V1a1 1 0 0 1 1-1zm1 2v10h6V2zm3 11a1 1 0 1 0 0 2 1 1 0 0 0 0-2z"/></svg>
      </li>
      <li>dana@kestrelnet.com
        <svg viewBox="0 0 16 16"><path d="M1 3h14v10H1zm1.5 1.2V12h11V4.2L8 8.5z M2.8 4 8 7.8 13.2 4z"/></svg>
      </li>
      <li>www.kestrelnet.com
        <svg viewBox="0 0 16 16"><path d="M8 0a8 8 0 1 0 0 16A8 8 0 0 0 8 0zm0 1.5c.9 0 1.9 1.9 2.2 5H5.8c.3-3.1 1.3-5 2.2-5zM1.6 6.5h2.7c.1-1.8.5-3.3 1.1-4.3a6.5 6.5 0 0 0-3.8 4.3zm0 3a6.5 6.5 0 0 0 3.8 4.3c-.6-1-1-2.5-1.1-4.3zm4.2 0c.3 3.1 1.3 5 2.2 5s1.9-1.9 2.2-5zm5.9 0c-.1 1.8-.5 3.3-1.1 4.3a6.5 6.5 0 0 0 3.8-4.3zm2.7-3a6.5 6.5 0 0 0-3.8-4.3c.6 1 1 2.5 1.1 4.3z"/></svg>
      </li>
    </ul>
  </div>
</section>

<section class="card card--back" aria-label="Business card back">
  <div class="back-ring"></div>
  <p class="back-brand">Kestrelnet</p>
</section>

</body>
</html>
```